Expedition Cruise Sales Website for the Polar Regions (Antarctica & Arctic)

This will be a website for selling cruises.
This site should have a homepage, a ship page, destinations, and itineraries.
I have created a file specifying each page, and it is attached.
Pages:
1. Home
2. Cruise Lines
- 2.1 Ships
3. Destinations
- 3.1 Region - 3.2 Country - 3.3 City
4. Itineraries
- 4.1 Itinerary
5. Blog / Travel Tips 6. About Us
7. Contact
Please take a look on the attached pdf
Target Market(s)
Expedition Travelers
Coding
Coded - Design and coding required
Number of Pages Required
5+ page
Font styles to use
Look and feel
Each slider illustrates characteristics of the customer's brand and the style your logo design should communicate.

```html
<!DOCTYPE html>
<html lang="en">
<head>
<meta charset="utf-8">
<title>Polarvo – FAQ</title>
<link href="https://fonts.googleapis.com/css2?family=Plus+Jakarta+Sans:wght@400;500;600;700&display=swap" rel="stylesheet">
<style>
:root{
  --navy:#0f1f3d;
  --blue:#3474b8;
  --blue-soft:#cfdcec;
  --muted:#7a8597;
  --line:#d6dde7;
  --gray-bg:#edf0f5;
  --footer:#1d2f52;
  --white:#ffffff;
}
*{box-sizing:border-box;margin:0;padding:0}
html,body{width:1200px;height:2874px;overflow:hidden}
body{position:relative;font-family:"Plus Jakarta Sans",sans-serif;color:var(--navy);background:var(--white)}
.abs{position:absolute}

/* hero */
.hero{left:0;top:0;width:1200px;height:312px;background:linear-gradient(100deg,#3d5a3a 0%,#5f6e5e 30%,#8c8e83 50%,#2f7e92 70%,#1d6a86 100%)}
.hero-shade{left:0;top:0;width:1200px;height:312px;background:linear-gradient(180deg,rgba(12,24,50,.65) 0%,rgba(12,24,50,.2) 45%,rgba(12,24,50,.1) 100%)}
.brand{display:flex;align-items:center;gap:8px;color:var(--white);font-weight:600}
.brand-dot{width:30px;height:30px;border-radius:50%;background:var(--white)}
.site-brand{left:65px;top:32px;font-size:28px}
.nav{left:378px;top:40px;font-size:9.5px;font-weight:500;color:var(--white)}
.nav a{color:inherit;text-decoration:none;position:absolute;white-space:nowrap}
.nav a.active{color:#6ea6e0}
.nav-phone{left:905px;top:41px;color:var(--white);font-size:12px;font-weight:600;display:flex;align-items:center;gap:5px}
.btn-book{left:1025px;top:33px;width:99px;height:31px;background:var(--blue);color:var(--white);font-size:10px;font-weight:600;display:flex;align-items:center;justify-content:center}
.hero-title{left:0;width:1200px;top:132px;text-align:center;color:var(--white);font-size:40px;font-weight:700}
.crumbs{left:0;width:1200px;top:191px;text-align:center;color:var(--white);font-size:11px;font-weight:500;word-spacing:8px}

/* faq */
.faq-top{left:0;top:312px;width:1200px;height:647px;background:linear-gradient(180deg,#ffffff 0%,var(--gray-bg) 100%)}
.faq-mid{left:0;top:959px;width:1200px;height:535px;background:var(--white)}
.faq-low{left:0;top:1494px;width:1200px;height:604px;background:linear-gradient(180deg,var(--gray-bg) 0%,#ffffff 100%)}
.main-title{left:0;width:1200px;top:362px;text-align:center;font-size:22px;font-weight:600}
.tabs{left:380px;top:419px;display:flex;gap:6px}
.tab{height:25px;padding:0 12px;background:var(--blue-soft);font-size:9px;font-weight:500;display:flex;align-items:center}
.group-title{left:0;width:1200px;text-align:center;font-size:19px;font-weight:600}
.accordion{left:293px;width:613px;display:flex;flex-direction:column;gap:13px}
.item{background:var(--white);border:1px solid var(--line);height:37px;display:flex;align-items:center;padding-left:50px;position:relative;font-size:11.5px;font-weight:600}
.item::before,.item::after{content:"";position:absolute;left:19px;top:17px;width:13px;height:1.5px;background:var(--blue)}
.item::after{transform:rotate(90deg)}
.item.open{height:80px;display:block;padding-top:12px}
.item.open::before{top:18px}
.item.open::after{display:none}
.item p{font-size:9.2px;font-weight:400;color:var(--muted);line-height:15px;margin-top:9px;width:476px}

/* newsletter */
.news-band{left:0;top:2098px;width:1200px;height:424px;background:var(--blue)}
.news-photo{left:706px;top:2042px;width:387px;height:480px;background:linear-gradient(180deg,#dfe3e7 0%,#b9c0c7 45%,#4a5259 60%,#9aa6b0 80%,#6b7782 100%)}
.news-title{left:106px;top:2186px;color:var(--white);font-size:30px;font-weight:400;line-height:35px}
.news-title b{font-weight:700}
.news-text{left:106px;top:2265px;width:376px;color:var(--white);font-size:12px;line-height:15px}
.field{width:235px;height:31px;background:var(--white);font-size:9px;font-weight:500;padding-left:14px;display:flex;align-items:center}
.btn-submit{left:106px;top:2412px;width:100px;height:31px;background:var(--navy);color:var(--white);font-size:10px;font-weight:600;display:flex;align-items:center;justify-content:center}

/* footer */
.footer{left:0;top:2522px;width:1200px;height:352px;background:linear-gradient(180deg,#22365c 0%,var(--footer) 100%)}
.foot-brand{left:106px;top:2601px;font-size:28px}
.foot-brand .brand-dot{width:38px;height:38px}
.foot-desc{left:106px;top:2659px;width:372px;color:var(--white);font-size:9.3px;line-height:19px}
.foot-h{color:var(--white);font-size:13px;font-weight:600}
.foot-list{color:var(--white);font-size:9px;line-height:19px;list-style:none}
.contact-line{color:var(--white);font-size:10px;display:flex;align-items:center;gap:8px}
.socials{left:588px;top:2722px;display:flex;gap:7px}
.social{width:31px;height:31px;border:1px solid var(--white);border-radius:50%}
.divider{left:106px;top:2802px;width:1017px;height:1px;background:rgba(255,255,255,.18)}
.copy{left:106px;top:2834px;color:var(--white);font-size:9px}
.copy b{font-weight:600}
.to-top{left:1128px;top:2795px}
.help{left:1056px;top:2497px;width:111px;height:49px;background:var(--white);border-radius:3px;padding:8px 9px;font-size:7px;font-weight:600;line-height:10px}
.help strong{color:var(--blue);font-size:13px}
.help-dot{left:1122px;top:2480px;width:34px;height:34px;border-radius:50%;background:#3fc251;border:3px solid var(--white)}
</style>
</head>
<body>

<div class="abs hero" role="img" aria-label="Rocky coastal cliffs with green vegetation above a beach and turquoise sea"></div>
<div class="abs hero-shade"></div>

<div class="abs brand site-brand"><span class="brand-dot"></span>Polarvo</div>
<nav class="abs nav">
  <a class="active" style="left:0">Home</a>
  <a style="left:64px">Cruise lines</a>
  <a style="left:152px">Destinations</a>
  <a style="left:243px">Itineraries</a>
  <a style="left:325px">Blog</a>
  <a style="left:384px">About us</a>
  <a style="left:461px">Contact</a>
</nav>
<div class="abs nav-phone">
  <svg width="10" height="10" viewBox="0 0 24 24"><path fill="#fff" d="M6.6 10.8a15.1 15.1 0 0 0 6.6 6.6l2.2-2.2c.3-.3.7-.4 1-.2 1.1.4 2.3.6 3.6.6.6 0 1 .4 1 1V20c0 .6-.4 1-1 1A17 17 0 0 1 3 4c0-.6.4-1 1-1h3.5c.6 0 1 .4 1 1 0 1.3.2 2.5.6 3.6.1.3 0 .7-.2 1z"/></svg>
  555.014.2290
</div>
<div class="abs btn-book">Book Now!</div>

<h1 class="abs hero-title">FAQ</h1>
<div class="abs crumbs">Home &gt;&gt; FAQ</div>

<section class="abs faq-top"></section>
<section class="abs faq-mid"></section>
<section class="abs faq-low"></section>

<h2 class="abs main-title">Frequently Asked Questions</h2>
<div class="abs tabs">
  <span class="tab">Reservations &amp; Payments</span>
  <span class="tab">Luggage &amp; Documentation</span>
  <span class="tab">Accommodations &amp; Services</span>
</div>

<h3 class="abs group-title" style="top:474px">Reservations &amp; Payments</h3>
<div class="abs accordion" style="top:529px">
  <div class="item open">Contrary to popular belief, lorem ipsum is not simply?<p>You stay in control. Lumen is physician-led by design. Your clinical decisions, care model, and practice culture remain yours. We support your growth – you lead the care.</p></div>
  <div class="item">There are many variations of passages of lorem ipsum available?</div>
  <div class="item">Sed ut perspiciatis unde omnis iste natus error?</div>
  <div class="item">At vero eos et accusamus et iusto odio dignissimos?</div>
  <div class="item">It is a long established fact that a reader will be distracted?</div>
  <div class="item">Sed ut perspiciatis unde omnis iste natus error?</div>
  <div class="item">Voluptatem accusantium doloremque laudantium?</div>
</div>

<h3 class="abs group-title" style="top:1009px">Luggage &amp; Documentation</h3>
<div class="abs accordion" style="top:1064px">
  <div class="item open">Contrary to popular belief, lorem ipsum is not simply?<p>You stay in control. Lumen is physician-led by design. Your clinical decisions, care model, and practice culture remain yours. We support your growth – you lead the care.</p></div>
  <div class="item">There are many variations of passages of lorem ipsum available?</div>
  <div class="item">Sed ut perspiciatis unde omnis iste natus error?</div>
  <div class="item">At vero eos et accusamus et iusto odio dignissimos?</div>
  <div class="item">It is a long established fact that a reader will be distracted?</div>
  <div class="item">Sed ut perspiciatis unde omnis iste natus error?</div>
  <div class="item">Voluptatem accusantium doloremque laudantium?</div>
</div>

<h3 class="abs group-title" style="top:1544px">Accommodations &amp; Services</h3>
<div class="abs accordion" style="top:1599px">
  <div class="item open">Contrary to popular belief, lorem ipsum is not simply?<p>You stay in control. Lumen is physician-led by design. Your clinical decisions, care model, and practice culture remain yours. We support your growth – you lead the care.</p></div>
  <div class="item">There are many variations of passages of lorem ipsum available?</div>
  <div class="item">Sed ut perspiciatis unde omnis iste natus error?</div>
  <div class="item">At vero eos et accusamus et iusto odio dignissimos?</div>
  <div class="item">It is a long established fact that a reader will be distracted?</div>
  <div class="item">Sed ut perspiciatis unde omnis iste natus error?</div>
  <div class="item">Voluptatem accusantium doloremque laudantium?</div>
</div>

<section class="abs news-band"></section>
<div class="abs news-photo" role="img" aria-label="Expedition cruise ship among ice floes beside snowy mountains"></div>
<h2 class="abs news-title">Get cruise deals <b>directly</b><br><b>in your inbox</b></h2>
<p class="abs news-text">Subscribe now and set sail on a journey of endless adventure with our exclusive cruise newsletter</p>
<div class="abs field" style="left:106px;top:2324px">First Name</div>
<div class="abs field" style="left:353px;top:2324px">Last Name</div>
<div class="abs field" style="left:106px;top:2368px">Email Address...</div>
<div class="abs field" style="left:353px;top:2368px">Whatsapp Number</div>
<div class="abs btn-submit">Submit</div>

<footer class="abs footer"></footer>
<div class="abs brand foot-brand"><span class="brand-dot"></span>Polarvo</div>
<p class="abs foot-desc">Lorem Ipsum is simply dummy text of the printing and typesetting industry. Lorem Ipsum has been the industry's standard dummy text ever since the 1500s, when an unknown printer took a galley of type and scrambled it to make a type specimen book.</p>

<div class="abs foot-h" style="left:588px;top:2594px">Contct Us</div>
<div class="abs contact-line" style="left:588px;top:2626px">
  <svg width="9" height="9" viewBox="0 0 24 24"><path fill="#fff" d="M6.6 10.8a15.1 15.1 0 0 0 6.6 6.6l2.2-2.2c.3-.3.7-.4 1-.2 1.1.4 2.3.6 3.6.6.6 0 1 .4 1 1V20c0 .6-.4 1-1 1A17 17 0 0 1 3 4c0-.6.4-1 1-1h3.5c.6 0 1 .4 1 1 0 1.3.2 2.5.6 3.6.1.3 0 .7-.2 1z"/></svg>
  <span style="font-size:11px">555.014.2290</span>
</div>
<div class="abs contact-line" style="left:588px;top:2652px">
  <svg width="9" height="9" viewBox="0 0 24 24"><path fill="#fff" d="M2 5h20v14H2z"/><path fill="none" stroke="#1d2f52" stroke-width="2" d="M2 5l10 8 10-8"/></svg>
  hello@polarvotrips.com
</div>
<div class="abs foot-h" style="left:588px;top:2692px">Follow us</div>
<div class="abs socials" aria-label="Social links">
  <span class="social" aria-label="Social profile 1"></span>
  <span class="social" aria-label="Social profile 2"></span>
  <span class="social" aria-label="Social profile 3"></span>
  <span class="social" aria-label="Social profile 4"></span>
</div>

<div class="abs foot-h" style="left:818px;top:2594px">Quick Links</div>
<ul class="abs foot-list" style="left:818px;top:2624px">
  <li>Home</li><li>Cruise Lines</li><li>Destinations</li><li>Itineraries</li><li>Blog</li><li>About Us</li><li>Contact</li>
</ul>
<ul class="abs foot-list" style="left:923px;top:2624px">
  <li>FAQ</li><li>Privacy Policy</li><li>Terms and Conditions</li><li>Booking Confirmation</li>
</ul>

<div class="abs divider"></div>
<div class="abs copy">© 2025 <b>Polarvo</b> All Rights Reserved</div>
<svg class="abs to-top" width="18" height="20" viewBox="0 0 18 20"><path fill="#fff" d="M9 0L18 20 9 14 0 20z"/></svg>

<div class="abs help">Available<br><strong>24/7</strong> to Assist with<br>Any Questions</div>
<div class="abs help-dot"></div>

</body>
</html>
```